VELTAR WEBSITE

need to create a new website for VELTAR ltd
the company deals with all aspects of safety products & safety wear
we need a simple website to show
ideas can be taken from following website whose products we shall distribute in kenya
www.kwr.co.uk
www.dorvik.eu
www.brimtoolsupplyco.com
www.gardvalewerks.co.za

we need following tabs
1) home - basic company information
2) products - broken down to following categories ie gloves, head protection, ear protection, mouth protection, foot protection
3) contacts

the company profile is a reputable company dealing with all aspects of safety, HSE (health and safety equipment), and PPE (personal protective equipment)

the website should have the dorvik logo for which we are an authorized distributor.
the dorvi industrial range writeup can be picked from their website
Updates

Dear Designers, i shall be able to choose a final design in 2 weeks, sorry i have not been able to finalise this due to a personal reason

Target Market(s)

the buyers are all types of industry who care for their employees safety

Industry/Entity Type

Industrial

Requirements
Must have
• clean look, fresh look, user freindly
Nice to have
• clear images, quick links etc

```html
<!DOCTYPE html>
<html lang="en">
<head>
<meta charset="utf-8">
<title>VELTAR — Safety Products &amp; Protective Wear</title>
<link rel="stylesheet" href="https://fonts.googleapis.com/css2?family=Open+Sans:wght@400;600;700&display=swap">
<style>
:root{
  --navy:#0f3346;
  --navy-dark:#0b2a3a;
  --orange:#f7a823;
  --text:#2b2b2b;
  --muted:#8a8a8a;
  --light:#f4f4f4;
  --line:#d8d8d8;
  --footer:#242424;
  --footer-bottom:#1c1c1c;
  --footer-text:#8f8f8f;
}
*{margin:0;padding:0;box-sizing:border-box}
html,body{width:867px;height:1200px;overflow:hidden}
body{font-family:"Open Sans",Arial,sans-serif;background:#fff;color:var(--text);position:relative}
.abs{position:absolute}

/* header */
.site-header{left:0;top:0;width:867px;height:100px;background:#f5f5f5}
.brand{left:84px;top:34px;display:flex;align-items:center;gap:8px}
.brand-mark{width:18px;height:18px;background:var(--orange)}
.brand-name{font-size:26px;font-weight:700;color:var(--navy);letter-spacing:1px}
.follow{left:505px;top:38px;display:flex;align-items:center;gap:4px;font-size:8.5px;color:#555}
.follow span.sq{width:12px;height:12px;background:#4a7fb5;display:inline-block}
.follow span.sq.rss{background:#e27a2b}
.follow b{font-weight:400;margin-right:4px}
.search{left:625px;top:36px;width:161px;height:18px;border:1px solid #ccc;background:#fff;border-radius:2px;font-size:9px;font-style:italic;color:#888;padding:3px 9px}
.search-btn{position:absolute;right:0;top:0;width:20px;height:16px;background:#eee;border-left:1px solid #ccc}

/* nav */
.main-nav{left:0;top:100px;width:867px;height:35px;background:var(--navy)}
.main-nav a{position:absolute;top:11px;font-size:10px;color:#fff;text-decoration:none;white-space:nowrap}
.main-nav a.active{font-weight:600}

/* hero */
.hero{left:0;top:135px;width:867px;height:380px;background:linear-gradient(90deg,#c9b24a 0%,#d8c873 30%,#b9c4c6 52%,#d9822e 70%,#c84a24 88%,#d8c9a8 100%)}
.hero-notch{left:0;top:514px}
.hero-caption{left:81px;top:245px;width:276px;height:146px;background:rgba(20,20,20,.85);padding:12px 13px}
.hero-caption h1{font-size:22px;font-weight:400;color:var(--orange);line-height:1.2}
.hero-caption h1 strong{font-weight:600}
.hero-caption p{font-size:10px;line-height:14.5px;color:#fff;margin-top:8px}
.dots{position:absolute;right:20px;bottom:10px;display:flex;gap:5px}
.dots i{width:5px;height:5px;background:#fff;display:block}

/* features */
.feature{top:568px;width:240px;height:228px;text-align:center}
.feature.highlight{background:#f6f6f6;box-shadow:0 1px 4px rgba(0,0,0,.15)}
.feature svg{display:block;margin:28px auto 0;height:46px}
.feature h2{font-size:13px;font-weight:400;color:var(--navy);margin-top:6px}
.feature.highlight h2{color:var(--orange)}
.feature p{font-size:9px;line-height:11.4px;color:var(--muted);margin:16px auto 0;width:182px}
.btn{display:inline-block;margin-top:25px;width:66px;height:22px;border:1px solid #ccc;background:linear-gradient(#fff,#eee);font-size:8.5px;color:#999;line-height:20px}

/* info band */
.info{left:0;top:841px;width:867px;height:194px;background:var(--light)}
.section-title{font-size:14.5px;font-weight:400;color:var(--navy)}
.title-rule{height:2px;background:var(--line);position:relative}
.title-rule::before{content:"";position:absolute;left:0;top:0;height:2px;background:var(--navy)}
.about-photo{left:85px;top:897px;width:169px;height:114px;background:linear-gradient(135deg,#5a7892,#3d5d7a 50%,#b6a04a)}
.about-text{left:264px;top:898px;width:270px;font-size:9.3px;line-height:14.5px;color:#9a9a9a}
.quote{left:580px;top:892px;font-size:26px;font-weight:700;color:var(--navy);font-style:italic;line-height:1}
.testimonial{left:597px;top:907px;width:180px;font-size:9.5px;line-height:12.4px;color:var(--text)}
.author{left:724px;top:976px;font-size:9.5px;color:var(--navy)}

/* footer */
.site-footer{left:0;top:1035px;width:867px;height:125px;background:var(--footer)}
.footer-col h3{font-size:10px;font-weight:400;color:#fff}
.footer-col ul{list-style:none;margin-top:9px}
.footer-col li,.footer-col p{font-size:9px;line-height:13.6px;color:var(--footer-text)}
.footer-col p{margin-top:9px;width:146px}
.socials{display:flex;gap:6px;margin-top:15px}
.socials i{width:17px;height:17px;display:block;border-radius:3px;background:#4a7fb5}
.socials i:nth-child(3){background:#c33}
.socials i:nth-child(4){background:#d44a3a}
.footer-bottom{left:0;top:1160px;width:867px;height:40px;background:var(--footer-bottom);text-align:center;font-size:9.5px;color:#ccc;line-height:40px}
</style>
</head>
<body>

<header class="site-header abs">
  <div class="brand abs"><span class="brand-mark"></span><span class="brand-name">VELTAR</span></div>
  <div class="follow abs"><b>Follow Us</b><span class="sq"></span><span class="sq"></span><span class="sq"></span><span class="sq rss"></span></div>
  <div class="search abs">Search<span class="search-btn"></span></div>
</header>

<nav class="main-nav abs">
  <a class="active" href="#" style="left:82px">HOME</a>
  <a href="#" style="left:145px">Head Protection</a>
  <a href="#" style="left:250px">Foot Protection</a>
  <a href="#" style="left:351px">Ear Protection</a>
  <a href="#" style="left:448px">Health and Safety Equipment</a>
  <a href="#" style="left:610px">Mouth Protection</a>
  <a href="#" style="left:721px">Contact Us</a>
</nav>

<section class="hero abs" role="img" aria-label="Worker in orange hard hat, yellow safety glasses and ear defenders in front of a yellow crane"></section>
<svg class="hero-notch abs" width="867" height="24" viewBox="0 0 867 24">
  <path d="M410 0 C440 0 450 10 456 22 C462 10 472 0 502 0 Z" fill="#c74a26"/>
  <path d="M410 0 C440 0 450 10 456 22 C462 10 472 0 502 0" fill="none" stroke="#f7a823" stroke-width="0"/>
</svg>

<div class="hero-caption abs">
  <h1><strong>Veltar</strong> Protection</h1>
  <p>It is a long established fact that a reader will be distracted by the readable content of a page when looking at its layout. The point of using Lorem Ipsum is that it has a more-or-less normal distribution of letters, as opposed to using 'Content here, content here',</p>
  <div class="dots"><i></i><i></i><i></i><i></i><i style="background:transparent"></i><i></i></div>
</div>

<article class="feature abs" style="left:95px">
  <svg viewBox="0 0 30 46" width="30"><path d="M6 14 C6 5 13 1 18 1 C25 1 29 7 29 14 C29 22 21 24 20 32 C19 40 15 44 10 44 C6 44 4 41 4 38" fill="none" stroke="#1d2f3a" stroke-width="3"/><path d="M12 15 C12 10 15 8 18 8 C22 8 23 12 23 14 C23 19 17 19 17 25" fill="none" stroke="#1d2f3a" stroke-width="2.5"/></svg>
  <h2>EAR PROTECTION</h2>
  <p>It is a long established fact that a reader will be distracted by the readable content of a page when looking at its layout. The point of using Lorem Ipsum is that it has a more-or-less normal distribution of letters.</p>
  <a class="btn">Read more</a>
</article>

<article class="feature highlight abs" style="left:333px">
  <svg viewBox="0 0 44 36" width="44" style="margin-top:30px;height:36px"><path d="M6 28 C6 12 14 3 24 3 C34 3 40 12 40 24 Z" fill="#f7a823"/><path d="M2 28 L42 26 L42 30 C30 33 14 34 2 32 Z" fill="#f7a823"/><path d="M22 4 C16 9 14 18 14 27" stroke="#fff" stroke-width="2" fill="none"/></svg>
  <h2>HEAD PROTECTION</h2>
  <p>It is a long established fact that a reader will be distracted by the readable content of a page when looking at its layout. The point of using Lorem Ipsum is that it has a more-or-less normal distribution of letters.</p>
  <a class="btn" style="margin-top:26px">Read more</a>
</article>

<article class="feature abs" style="left:582px">
  <svg viewBox="0 0 40 44" width="36"><g fill="#1d2f3a"><rect x="3" y="10" width="5" height="20" rx="2"/><rect x="10" y="5" width="5" height="24" rx="2"/><rect x="17" y="3" width="5" height="26" rx="2"/><rect x="24" y="6" width="5" height="24" rx="2"/><path d="M4 26 H30 L34 16 L38 18 L32 38 H8 Z"/></g></svg>
  <h2>GLOVES</h2>
  <p>It is a long established fact that a reader will be distracted by the readable content of a page when looking at its layout. The point of using Lorem Ipsum is that it has a more-or-less normal distribution of letters.</p>
  <a class="btn">Read more</a>
</article>

<section class="info abs"></section>
<h2 class="section-title abs" style="left:85px;top:861px">About Us</h2>
<div class="title-rule abs" style="left:85px;top:882px;width:449px"></div>
<style>.info ~ .title-rule:nth-of-type(1)::before{}</style>
<div class="abs" style="left:85px;top:882px;width:80px;height:2px;background:var(--navy)"></div>
<div class="about-photo abs" role="img" aria-label="Worker in face shield and blue overalls using a power tool in a workshop"></div>
<p class="about-text abs">Lorem Ipsum is simply dummy text of the printing and typesetting industry. Lorem Lorem Ipsum is simply dummy text of the printing and typesetting industry. Lorem Lorem Ipsum is simply dummy text of the printing and typesetting industry. Lorem Ipsum is simply dummy text of the printing and typesetting industry. Lorem Lorem Ipsum is simply dummy text of the printing and typesetting industry. Lorem Lorem Ipsum is simply dummy text of the printing and typesetting industry.</p>

<h2 class="section-title abs" style="left:580px;top:860px">Our Testimonials</h2>
<div class="abs" style="left:580px;top:882px;width:204px;height:2px;background:var(--line)"></div>
<div class="abs" style="left:580px;top:882px;width:46px;height:2px;background:var(--navy)"></div>
<span class="quote abs">“</span>
<p class="testimonial abs">Lorem Ipsum is simply dummy text of the printing and typesetting industry. Lorem Lorem Ipsum is simply dummy text of the printing and typesetting industry. Lorem Lorem Ipsum is simply dummy text of the</p>
<span class="quote abs" style="left:771px;top:962px">”</span>
<span class="author abs">Marlo Kent</span>

<footer class="site-footer abs">
  <div class="footer-col abs" style="left:98px;top:18px"><h3>Our Services</h3><ul><li>Game Servers</li><li>Dedicated Servers</li></ul></div>
  <div class="footer-col abs" style="left:282px;top:18px"><h3>Support</h3><ul><li>Contact Us</li></ul></div>
  <div class="footer-col abs" style="left:463px;top:18px"><h3>Our Company</h3><ul><li>About US</li><li>FAQs</li><li>Testimonials</li></ul></div>
  <div class="footer-col abs" style="left:636px;top:18px"><h3>Veltar</h3><p>It is a long established fact that a reader will be distracted by the readable content of a page</p>
    <div class="socials"><i></i><i></i><i></i><i></i></div></div>
</footer>
<div class="footer-bottom abs">©2003 Veltar Protection, Inc. | &nbsp; All rights reserved.</div>

</body>
</html>
```